1 Page for Computer Repair Website

Looking for a 1 page website with a design that compliments the business card and pamphlet that have already been made (attached files). It should look business professional and easy to read. Email and phone number should be somewhere near the top of the website, visible when the page loads. I don't want any forms for people to mess with. No "Contact Us" form or entering in email for newsletter. Customers will just be looking at this site to confirm we are professionals and have our business in order.

Target Market(s)

Home and small business

Industry/Entity Type

Computer Repair

Coding

Coded - Design and coding required

Number of Pages Required

1 page

Font styles to use
Other font styles liked:
• Helvetica variations used in pamphlet and card

Colors
0455a3
cfdeed
85abd2
3276b5
85cae6
ffffff

Requirements
Must have
• Compliment the pamphlet and business card in color choices and font use. Pleasing to the eye and easy to read through categories and text.
Should not have
• Forms. No "enter name and email here" or anything of the sort.

```html
<!DOCTYPE html>
<html lang="en">
<head>
<meta charset="utf-8">
<title>NEXBIT Computer Services</title>
<link href="https://fonts.googleapis.com/css2?family=Roboto:wght@300;400;500;700&display=swap" rel="stylesheet">
<style>
:root{
  --blue:#0455a3;
  --blue-mid:#3276b5;
  --blue-soft:#85abd2;
  --blue-sky:#85cae6;
  --blue-pale:#cfdeed;
  --white:#ffffff;
  --ink:#3d3d3d;
  --muted:#6b6b6b;
  --band:#eef3f8;
  --dark:#2f3236;
  --line:#c9d6e4;
}
*{box-sizing:border-box;margin:0;padding:0}
html,body{width:1200px;height:2500px;overflow:hidden}
body{font-family:"Roboto",Helvetica,Arial,sans-serif;color:var(--ink);background:var(--white);font-size:13px;line-height:1.6}
.topbar{height:24px;background:var(--dark);color:#d9d9d9;font-size:11px;display:flex;justify-content:space-between;align-items:center;padding:0 40px}
.topbar span{display:flex;align-items:center;gap:6px}
.header{height:100px;display:flex;align-items:center;justify-content:space-between;padding:0 40px 0 100px}
.brand{display:flex;align-items:center;gap:12px;color:var(--blue);font-weight:700;font-size:34px;letter-spacing:1px;line-height:1}
.brand-mark{width:14px;height:14px;background:var(--blue)}
.brand small{display:block;font-size:14px;font-weight:700;letter-spacing:0.5px;margin-top:2px}
.nav{display:flex;gap:26px;font-size:12px;font-weight:500;color:var(--blue)}
.nav .active{border-bottom:2px solid var(--blue);padding-bottom:4px}
.hero{position:relative;height:576px;color:var(--white);text-align:center}
.hero-photo{position:absolute;inset:0;background:linear-gradient(160deg,#6a7078 0%,#3a3f46 45%,#1f2226 100%)}
.hero-body{position:absolute;left:0;right:0;top:225px}
.hero h1{font-weight:400;font-size:36px;letter-spacing:1px}
.hero p{width:620px;margin:8px auto 18px;font-size:12px;color:#e4e4e4;line-height:1.5}
.btn-outline{display:inline-block;border:1px solid var(--white);padding:6px 18px;font-size:11px;letter-spacing:1px}
.arrow{position:absolute;top:270px;width:34px;height:34px;border-radius:50%;background:rgba(255,255,255,0.85);display:flex;align-items:center;justify-content:center}
.arrow.left{left:18px}.arrow.right{right:18px}
.heading{display:flex;align-items:center;justify-content:center;gap:22px;color:var(--blue);font-size:32px;font-weight:400;letter-spacing:1px}
.heading::before,.heading::after{content:"";width:60px;height:1px;background:var(--blue)}
.about{height:310px;padding-top:68px;text-align:center}
.about p{width:880px;margin:22px auto 24px;font-size:12px;color:var(--muted)}
.btn-solid{display:inline-block;background:var(--blue);color:var(--white);padding:9px 22px;font-size:12px;letter-spacing:1px}
.services{height:640px;background:var(--band);padding-top:58px}
.service-grid{display:grid;grid-template-columns:1fr 1fr;column-gap:80px;row-gap:34px;width:1000px;margin:44px auto 0}
.service{display:flex;gap:18px;align-items:flex-start}
.service-icon{flex:none;width:70px;height:70px;border:1px solid var(--line);background:var(--white);display:flex;align-items:center;justify-content:center}
.service h3{font-size:15px;font-weight:500;color:var(--blue);margin:6px 0 4px}
.service p{font-size:11.5px;color:var(--muted);line-height:1.5}
.why{height:500px;padding-top:50px}
.why-body{display:flex;gap:70px;width:1000px;margin:40px auto 0;align-items:flex-start}
.why-image{flex:none;width:420px;height:270px;margin-top:20px;background:linear-gradient(180deg,#e8ecf0 0%,#c9ced4 100%)}
.why-list{list-style:none;flex:1}
.why-list li{display:flex;gap:10px;font-size:12px;color:var(--muted);margin-bottom:12px;line-height:1.45}
.why-list svg{flex:none;margin-top:2px}
.testimonials{height:290px;background:var(--band);padding-top:40px;position:relative}
.quotes{display:flex;gap:40px;width:1000px;margin:30px auto 0}
.quote{flex:1}
.quote-box{background:var(--white);border:1px solid var(--line);padding:16px 20px;font-size:11.5px;color:var(--muted);line-height:1.55}
.quote-author{display:flex;align-items:center;gap:12px;margin-top:14px;font-size:11px;font-weight:500;color:var(--ink);letter-spacing:0.5px}
.avatar{width:38px;height:38px;border-radius:50%;background:linear-gradient(135deg,#b9c2cc,#7d8893)}
.t-arrow{position:absolute;top:150px;width:26px;height:26px;border-radius:50%;background:var(--blue-pale);display:flex;align-items:center;justify-content:center}
.t-arrow.left{left:40px}.t-arrow.right{right:40px}
.footer{height:160px;background:var(--dark);color:#cfcfcf;font-size:11px;display:flex;justify-content:space-between;align-items:flex-start;padding:40px 40px 0}
.social{display:flex;align-items:center;gap:8px}
.social i{display:block;width:14px;height:14px;background:#7a8088}
</style>
</head>
<body>
<div class="topbar">
  <span><svg width="12" height="9" viewBox="0 0 12 9"><rect x="0.5" y="0.5" width="11" height="8" fill="none" stroke="#d9d9d9"/><path d="M0.5 0.5 6 5 11.5 0.5" fill="none" stroke="#d9d9d9"/></svg>help@nexbitrepair.com</span>
  <span><svg width="10" height="10" viewBox="0 0 10 10"><path d="M2 0.5 4 3 3 4.2q1 2 2.8 2.8L7 6l2.5 2-1 1.5Q3 9 0.5 1.5Z" fill="#d9d9d9"/></svg>(555) 014-2290</span>
</div>
<header class="header">
  <div class="brand"><span class="brand-mark"></span><div>NEXBIT<small>Computer Services</small></div></div>
  <nav class="nav"><span class="active">HOME</span><span>ABOUT US</span><span>SERVICES</span><span>PROJECTS</span><span>NEWS</span><span>CONTACT US</span></nav>
</header>
<section class="hero">
  <div class="hero-photo" role="img" aria-label="Close-up photo of a dark keyboard with small figures of repair workers in orange overalls"></div>
  <div class="arrow left"><svg width="10" height="14"><path d="M8 1 2 7l6 6" fill="none" stroke="#333" stroke-width="2"/></svg></div>
  <div class="arrow right"><svg width="10" height="14"><path d="M2 1l6 6-6 6" fill="none" stroke="#333" stroke-width="2"/></svg></div>
  <div class="hero-body">
    <h1>COMPUTER SERVICE &amp; REPAIR COMPANY</h1>
    <p>We repair, upgrade and maintain computers for homes and small businesses, with honest pricing and fast turnaround.</p>
    <span class="btn-outline">CLICK HERE</span>
  </div>
</section>
<section class="about">
  <h2 class="heading">ABOUT US</h2>
  <p>We are a local computer repair team serving homes and small businesses. Our technicians fix hardware faults, remove viruses, recover lost files and set up new equipment so you can get back to work. We explain every repair in plain language, quote before we start, and stand behind our work with a clear service guarantee for every customer we help.</p>
  <span class="btn-solid">VIEW MORE</span>
</section>
<section class="services">
  <h2 class="heading">OUR SERVICES</h2>
  <div class="service-grid">
    <div class="service"><div class="service-icon"><svg width="40" height="36" viewBox="0 0 40 36"><rect x="2" y="2" width="36" height="24" fill="none" stroke="#0455a3" stroke-width="3"/><path d="M14 34h12M20 26v8M12 14l5 5 11-10" fill="none" stroke="#0455a3" stroke-width="3"/></svg></div><div><h3>HONEST SERVICE</h3><p>Our certified technicians work quickly and quote every job upfront, so there are no surprises.</p></div></div>
    <div class="service"><div class="service-icon"><svg width="34" height="40" viewBox="0 0 34 40"><path d="M17 2 31 7v12c0 9-6 16-14 19C9 35 3 28 3 19V7Z" fill="none" stroke="#0455a3" stroke-width="3"/><path d="M11 14l12 12M23 14 11 26" stroke="#0455a3" stroke-width="3"/></svg></div><div><h3>MALWARE/VIRUS REMOVAL</h3><p>We find and remove viruses, spyware and adware, then protect your system from new threats.</p></div></div>
    <div class="service"><div class="service-icon"><svg width="40" height="36" viewBox="0 0 40 36"><rect x="6" y="4" width="28" height="18" fill="none" stroke="#0455a3" stroke-width="3"/><path d="M2 28h36" stroke="#0455a3" stroke-width="4"/></svg></div><div><h3>PC/MAC/LAPTOP HARDWARE REPAIR</h3><p>Cracked screens, failed drives, dead power supplies and loose ports repaired on all major brands.</p></div></div>
    <div class="service"><div class="service-icon"><svg width="36" height="36" viewBox="0 0 36 36"><path d="M18 30V8M9 16l9-9 9 9" fill="none" stroke="#0455a3" stroke-width="4"/></svg></div><div><h3>UPGRADES</h3><p>Add memory, faster storage or a new graphics card to give an older computer new life.</p></div></div>
    <div class="service"><div class="service-icon"><svg width="40" height="36" viewBox="0 0 40 36"><rect x="3" y="4" width="12" height="28" fill="none" stroke="#0455a3" stroke-width="3"/><rect x="25" y="4" width="12" height="28" fill="none" stroke="#0455a3" stroke-width="3"/><path d="M16 18h8" stroke="#0455a3" stroke-width="3"/></svg></div><div><h3>DATA MIGRATION</h3><p>We move your files, email, settings and programs from your old computer to your new one.</p></div></div>
    <div class="service"><div class="service-icon"><svg width="38" height="38" viewBox="0 0 38 38"><circle cx="19" cy="19" r="5" fill="#0455a3"/><g stroke="#0455a3" stroke-width="3"><path d="M19 3v8M19 27v8M3 19h8M27 19h8"/></g><g fill="#0455a3"><circle cx="19" cy="3" r="3"/><circle cx="19" cy="35" r="3"/><circle cx="3" cy="19" r="3"/><circle cx="35" cy="19" r="3"/></g></svg></div><div><h3>DATA RESCUE</h3><p>Failed drive or deleted folder? We recover photos, documents and business records whenever possible.</p></div></div>
    <div class="service"><div class="service-icon"><svg width="38" height="36" viewBox="0 0 38 36"><path d="M3 17 19 3l16 14" fill="none" stroke="#0455a3" stroke-width="3"/><path d="M8 14v19h22V14" fill="none" stroke="#0455a3" stroke-width="3"/><rect x="15" y="20" width="8" height="13" fill="#0455a3"/></svg></div><div><h3>IN-HOME INSTALLATION</h3><p>We set up computers, printers and wireless networks in your home or office at a time that suits you.</p></div></div>
    <div class="service"><div class="service-icon"><svg width="40" height="36" viewBox="0 0 40 36"><rect x="2" y="2" width="36" height="22" fill="none" stroke="#0455a3" stroke-width="3"/><circle cx="20" cy="12" r="4" fill="#0455a3"/><path d="M12 34c0-6 4-9 8-9s8 3 8 9" fill="#0455a3"/></svg></div><div><h3>REMOTE SUPPORT</h3><p>Quick fixes done online through a secure connection, so you stay productive without waiting for a visit.</p></div></div>
  </div>
</section>
<section class="why">
  <h2 class="heading">WHY CHOOSE US</h2>
  <div class="why-body">
    <div class="why-image" role="img" aria-label="Photo of a laptop showing the company name on its screen"></div>
    <ul class="why-list">
      <li><svg width="12" height="12"><path d="M1 6l4 4 6-9" fill="none" stroke="#0455a3" stroke-width="2"/></svg>Fast turnaround on most repairs, often within the same working day.</li>
      <li><svg width="12" height="12"><path d="M1 6l4 4 6-9" fill="none" stroke="#0455a3" stroke-width="2"/></svg>Clear quotes given before any work begins, with no hidden fees.</li>
      <li><svg width="12" height="12"><path d="M1 6l4 4 6-9" fill="none" stroke="#0455a3" stroke-width="2"/></svg>Friendly technicians who explain every problem in plain, simple language.</li>
      <li><svg width="12" height="12"><path d="M1 6l4 4 6-9" fill="none" stroke="#0455a3" stroke-width="2"/></svg>Genuine parts and tested components used in every hardware repair.</li>
      <li><svg width="12" height="12"><path d="M1 6l4 4 6-9" fill="none" stroke="#0455a3" stroke-width="2"/></svg>Repairs for desktops, laptops and all major operating systems.</li>
      <li><svg width="12" height="12"><path d="M1 6l4 4 6-9" fill="none" stroke="#0455a3" stroke-width="2"/></svg>On-site visits available for homes and small business offices.</li>
      <li><svg width="12" height="12"><path d="M1 6l4 4 6-9" fill="none" stroke="#0455a3" stroke-width="2"/></svg>Your files and personal data handled with complete care and privacy.</li>
      <li><svg width="12" height="12"><path d="M1 6l4 4 6-9" fill="none" stroke="#0455a3" stroke-width="2"/></svg>Every repair backed by our straightforward service guarantee.</li>
    </ul>
  </div>
</section>
<section class="testimonials">
  <h2 class="heading">TESTIMONIALS</h2>
  <div class="t-arrow left"><svg width="8" height="12"><path d="M6 1 2 6l4 5" fill="none" stroke="#0455a3" stroke-width="2"/></svg></div>
  <div class="t-arrow right"><svg width="8" height="12"><path d="M2 1l4 5-4 5" fill="none" stroke="#0455a3" stroke-width="2"/></svg></div>
  <div class="quotes">
    <div class="quote">
      <div class="quote-box">The team fixed my laptop the same day and explained exactly what had gone wrong. The price was fair, the service was friendly and my computer runs faster than it has in years. I will be recommending them to everyone I know.</div>
      <div class="quote-author"><span class="avatar" role="img" aria-label="Customer portrait"></span>DANIEL R. PRICE</div>
    </div>
    <div class="quote">
      <div class="quote-box">Our office network kept dropping out until they came in and sorted it. They were punctual, tidy and patient with all our questions. Having a reliable local technician has taken a real weight off our small business.</div>
      <div class="quote-author"><span class="avatar" role="img" aria-label="Customer portrait"></span>MARK HOLDEN</div>
    </div>
  </div>
</section>
<footer class="footer">
  <span>All Copy Rights reserved</span>
  <div class="social"><span>Connect With Our Social Network</span><i></i><i></i><i></i><i></i><i></i></div>
</footer>
</body>
</html>
```